Business Card Design Project

I would like a business card created for a new company. This is a holding company that acts as my investment company. It holds real estate and service based companies. The name of the company is Sorvantica which is Italian for Evolution. Defined as development or growth.
We currently have no logo. I really like some of the "different" cards out there. Potentially metallic or grey/black. That looks premium/hi-end and unique. I am not sure if your design would be specific to the card stock I end with our just logo/design/font.
Industry/Entity Type
Real Estate
Look and feel

```html
<!DOCTYPE html>
<html lang="en">
<head>
<meta charset="utf-8">
<title>Sorvantica Business Card</title>
<link rel="stylesheet" href="https://fonts.googleapis.com/css2?family=Cinzel:wght@400;500&display=swap">
<style>
  :root {
    --page-bg: #ffffff;
    --card-bg: #020202;
    --silver-light: #f4f4f4;
    --silver-mid: #c9c9c9;
    --silver-dark: #8e8e8e;
    --text-shadow: rgba(255, 255, 255, 0.18);
  }
  * { margin: 0; padding: 0; box-sizing: border-box; }
  html, body {
    width: 1200px;
    height: 754px;
    overflow: hidden;
    background: var(--page-bg);
  }
  .card {
    position: absolute;
    left: 26px;
    top: 26px;
    width: 1150px;
    height: 700px;
    border-radius: 34px;
    background: var(--card-bg);
    font-family: "Cinzel", serif;
    color: var(--silver-mid);
  }
  .brand {
    position: absolute;
    left: 70px;
    top: 178px;
    display: flex;
    align-items: center;
    gap: 18px;
  }
  .brand-dot {
    width: 40px;
    height: 40px;
    border-radius: 50%;
    background: var(--silver-mid);
  }
  .brand-name {
    font-size: 54px;
    font-weight: 400;
    letter-spacing: 4px;
    color: var(--silver-mid);
    line-height: 1;
  }
  .holder-name {
    position: absolute;
    left: 0;
    width: 100%;
    top: 352px;
    padding-left: 12px;
    text-align: center;
    font-size: 76px;
    font-weight: 400;
    letter-spacing: 7px;
    line-height: 1;
    background: linear-gradient(180deg, var(--silver-light) 0%, var(--silver-mid) 55%, var(--silver-dark) 100%);
    -webkit-background-clip: text;
    background-clip: text;
    color: transparent;
    filter: drop-shadow(1px 1px 0 var(--text-shadow));
  }
  .contact {
    position: absolute;
    left: 434px;
    top: 578px;
    list-style: none;
    font-size: 29px;
    letter-spacing: 3.5px;
    line-height: 54px;
    color: var(--silver-light);
  }
</style>
</head>
<body>
  <main class="card">
    <div class="brand">
      <span class="brand-dot"></span>
      <span class="brand-name">Sorvantica</span>
    </div>
    <h1 class="holder-name">Your Name</h1>
    <ul class="contact">
      <li class="contact-phone">Phone:5555-5555</li>
      <li class="contact-email">Email: info@sorvantica.com</li>
    </ul>
  </main>
</body>
</html>
```